Brell Stone Company Business Cards

Front and Back Business Card - logo and text setup - cool design. I need workable photoshop or illustrator files so I can setup each employee card with design that is created
Updates

Hi everyone, thank you for the great entries. Please no more white and blue cards - there are so many already - black and silver only now please. thanks!

Target Market(s)

Construction Industry - Facility Managers

Industry/Entity Type

Construction

Contact Information for Business Card

I really like contemporary simplistic looks - clean neat....not opposed to seeing some black backrounds

Requirements
Must have
• Logo/website address with design on front only - www.brellstone-example.com (logo attached)
• Back:
• Name/Title/Company Address/Phone/email address
Nice to have
• Cool design
Should not have
• Nothing gimmicky like Fire or Water - since we are a Fire Protection company - it has all been done

```html
<!DOCTYPE html>
<html lang="en">
<head>
<meta charset="utf-8">
<title>Brell Stone Company Business Cards</title>
<link href="https://fonts.googleapis.com/css2?family=Maven+Pro:wght@400;500;700&display=swap" rel="stylesheet">
<style>
  :root {
    --page-bg: #141414;
    --card-bg: #171717;
    --text-light: #f2f2f2;
    --accent-orange: #e8472e;
    --accent-navy: #2a3f7a;
  }
  html, body {
    margin: 0;
    padding: 0;
    width: 1200px;
    height: 1000px;
    overflow: hidden;
    background: var(--page-bg);
    font-family: "Maven Pro", sans-serif;
    color: var(--text-light);
  }
  .canvas {
    position: relative;
    width: 1200px;
    height: 1000px;
  }
  .card {
    position: absolute;
    background: var(--card-bg);
    box-shadow: 0 10px 30px rgba(0,0,0,0.45);
  }
  .card-front {
    left: 275px;
    top: 88px;
    width: 650px;
    height: 370px;
  }
  .front-brand {
    position: absolute;
    left: 0;
    right: 0;
    top: 150px;
    text-align: center;
    font-size: 40px;
    font-weight: 700;
    color: var(--accent-orange);
    letter-spacing: 1px;
  }
  .front-web {
    position: absolute;
    left: 0;
    right: 0;
    top: 325px;
    text-align: center;
    font-size: 14px;
    letter-spacing: 5px;
    color: var(--text-light);
  }
  .card-back {
    left: 275px;
    top: 529px;
    width: 652px;
    height: 372px;
    overflow: hidden;
  }
  .back-brand {
    position: absolute;
    left: 45px;
    top: 38px;
    font-size: 40px;
    font-weight: 700;
    color: var(--accent-orange);
  }
  .person {
    position: absolute;
    right: 47px;
    top: 145px;
    text-align: right;
  }
  .person-name {
    font-size: 24px;
    line-height: 28px;
    letter-spacing: 0.5px;
  }
  .person-name .first { font-weight: 700; color: var(--text-light); }
  .person-name .last { font-weight: 400; color: var(--accent-orange); }
  .person-title {
    font-size: 15px;
    line-height: 18px;
  }
  .person-title .company { color: var(--accent-orange); }
  .divider {
    position: absolute;
    left: 45px;
    right: 47px;
    top: 207px;
    height: 1px;
    background: var(--accent-orange);
  }
  .contact-list {
    position: absolute;
    left: 45px;
    top: 222px;
    margin: 0;
    padding: 0;
    list-style: none;
  }
  .contact-list li {
    display: flex;
    align-items: center;
    height: 26.5px;
    font-size: 16px;
    letter-spacing: 0.3px;
  }
  .contact-list svg {
    width: 17px;
    height: 17px;
    margin-right: 10px;
    flex: none;
  }
  .address {
    position: absolute;
    right: 47px;
    top: 274px;
    text-align: right;
    font-size: 16px;
    line-height: 28px;
    letter-spacing: 0.3px;
  }
  .bottom-band {
    position: absolute;
    left: 0;
    bottom: 0;
    width: 652px;
    height: 13px;
  }
</style>
</head>
<body>
<div class="canvas">

  <section class="card card-front" aria-label="Card front">
    <div class="front-brand">Brell Stone</div>
    <div class="front-web">WWW.BRELLSTONE-EXAMPLE.COM</div>
  </section>

  <section class="card card-back" aria-label="Card back">
    <div class="back-brand">Brell Stone</div>

    <div class="person">
      <div class="person-name"><span class="first">MARCUS</span> <span class="last">LENN</span></div>
      <div class="person-title">CEO of <span class="company">brellstone</span></div>
    </div>

    <div class="divider"></div>

    <ul class="contact-list">
      <li>
        <svg viewBox="0 0 24 24" aria-hidden="true"><path fill="#e8472e" d="M6.6 10.8c1.4 2.8 3.8 5.1 6.6 6.6l2.2-2.2c.3-.3.7-.4 1-.2 1.1.4 2.3.6 3.6.6.6 0 1 .4 1 1V20c0 .6-.4 1-1 1C10.6 21 3 13.4 3 4c0-.6.4-1 1-1h3.5c.6 0 1 .4 1 1 0 1.3.2 2.5.6 3.6.1.3 0 .7-.2 1l-2.3 2.2z"/></svg>
        (02) 5550 1234
      </li>
      <li>
        <svg viewBox="0 0 24 24" aria-hidden="true"><rect x="6" y="2" width="12" height="20" rx="2" fill="none" stroke="#e8472e" stroke-width="2"/><circle cx="12" cy="18" r="1.3" fill="#e8472e"/></svg>
        0400 555 012
      </li>
      <li>
        <svg viewBox="0 0 24 24" aria-hidden="true"><rect x="2" y="5" width="20" height="14" rx="1.5" fill="#e8472e"/><path d="M3 6l9 7 9-7" fill="none" stroke="#171717" stroke-width="1.8"/></svg>
        info@brellstone-example.com
      </li>
      <li>
        <svg viewBox="0 0 24 24" aria-hidden="true"><circle cx="12" cy="12" r="10" fill="none" stroke="#e8472e" stroke-width="2"/><path d="M2 12h20M12 2c3 3 3 17 0 20M12 2c-3 3-3 17 0 20" fill="none" stroke="#e8472e" stroke-width="1.6"/></svg>
        www.brellstone-example.com
      </li>
    </ul>

    <div class="address">
      118/4 Harlow Rd, Westbrook<br>
      NSW 2199
    </div>

    <svg class="bottom-band" viewBox="0 0 652 13" aria-hidden="true">
      <polygon points="0,0 490,0 486,13 0,13" fill="var(--accent-orange)"/>
      <polygon points="495,0 652,0 652,13 491,13" fill="var(--accent-navy)"/>
    </svg>
  </section>

</div>
</body>
</html>
```